Design website for new email startup

We are starting a company called Pingo.QZ (it will live at http://pingo.qz).

We would like the main landing page for our site designed. We have provided a very simple wireframe to help provide direction for the content it should include, but we do not expect the designers to adhere to it at all - we encourage unique ideas. There is some sample text in the wireframe - this does not have to be used, but may provide ideas.

We provide an easy way for people to manage email for a custom domain name. For example if you own "yourhouseword.example" you can point your DNS records to us and we'll make it easy to have emails addressed to your domain get forwarded to your existing email (gmail, etc). Folks running blogs, and other small sites can quickly setup email addresses for their domains and manage them in one place.

(For technical folks, we have you point your dns mx records to us, hence the name. That way all your email hits us and we can redirect it wherever you want. We make it easy to manage a single domain or a bunch of domains. Many domain registrars offer this service for a fee, and have clumsy management tools. We provide a robust simple toolset for free, as well as premium options).

The goal of the landing page is to get folks into the signup flow. The second priority flow is to have them take a look at the premium plan offerings.

We may offer the winning designer additional work for the remainder of the site design.
Updates

I've changed this project to a committed payment.  It is no longer refundable.  Thank you.

Target Market(s)

Bloggers, podcasters, designers, app developers - people who are a little tech savvy.

Industry/Entity Type

It Company

Font styles to use
Sans Serif

Colors

Designer to choose colors to be used in the design.

Requirements
Must have
• A full fidelity mockup (comp) of the landing page including the source file (psd, ai, etc).

Some sort of logo treatment for the pingo.qz brand

A call to action for signup, such as the suggested 'Get Started Here'
Nice to have
• A hip startup feel

Incorporation of the email theme

Give the impression it is simple, easy and fast

```html
<!DOCTYPE html>
<html lang="en">
<head>
<meta charset="utf-8">
<title>Pingo.QZ – Email for your domain</title>
<link rel="stylesheet" href="https://fonts.googleapis.com/css2?family=Arimo:wght@400;700&family=PT+Sans:wght@400;700&display=swap">
<style>
  :root {
    --header-bg: #f8f8f8;
    --ink: #111111;
    --ink-soft: #222222;
    --accent: #f7891f;
    --hero-dark: #2e3a44;
    --hero-mid: #5f6f7a;
    --hero-light: #a7b3b9;
    --white: #ffffff;
    --card-bg: #ececec;
    --button-face: #f2f2f2;
    --button-edge: #c9c9c9;
    --footer-bg: #1c1c1c;
    --footer-text: #bdbdbd;
    --social: #5a5a5a;
  }
  * { box-sizing: border-box; margin: 0; padding: 0; }
  html, body { width: 1200px; height: 921px; overflow: hidden; background: var(--white); }
  body { font-family: "Arimo", Arial, sans-serif; color: var(--ink); position: relative; }

  .site-header { position: absolute; left: 0; top: 0; width: 1200px; height: 98px; background: var(--header-bg); }
  .brand { position: absolute; left: 122px; top: 34px; display: flex; align-items: center; gap: 8px;
    font-family: "Arimo", Arial, sans-serif; font-weight: 700; font-size: 30px; letter-spacing: 0.5px; color: var(--ink); line-height: 1; }
  .brand-mark { width: 12px; height: 12px; background: var(--accent); }
  .contact-phone { position: absolute; right: 127px; top: 27px; font-size: 13px; color: var(--ink-soft); display: flex; align-items: center; gap: 8px; }
  .main-nav { position: absolute; right: 127px; top: 65px; display: flex; gap: 31px; font-size: 15px; }
  .main-nav a { color: var(--ink); text-decoration: none; }

  .hero { position: absolute; left: 0; top: 98px; width: 1200px; height: 368px;
    background: linear-gradient(90deg, var(--hero-mid) 0%, var(--hero-dark) 25%, var(--hero-mid) 55%, var(--hero-light) 80%, var(--hero-mid) 100%); overflow: hidden; }
  .hero-points { position: absolute; left: 123px; top: 74px; list-style: none; }
  .hero-points li { display: flex; align-items: center; gap: 14px; color: var(--white); font-size: 14px; height: 30px; }
  .hero-points li:nth-child(3) { margin-top: 0; }
  .tick { width: 13px; height: 13px; flex: none; }
  .cta { position: absolute; top: 235px; height: 39px; display: flex; align-items: center;
    font-family: "PT Sans", Arial, sans-serif; font-weight: 700; font-size: 14px; color: var(--ink); text-decoration: none;
    background: linear-gradient(var(--white), var(--button-face) 60%, var(--button-edge)); }
  .cta-start { left: 122px; width: 179px; padding-left: 21px; clip-path: polygon(0 0, 90% 0, 100% 50%, 90% 100%, 0 100%); }
  .cta-plans { left: 311px; width: 181px; padding-left: 53px; clip-path: polygon(10% 0, 100% 0, 100% 100%, 10% 100%, 0 50%); }
  .slider-dots { position: absolute; left: 124px; top: 333px; display: flex; gap: 3px; }
  .slider-dots span { width: 9px; height: 9px; border-radius: 50%; background: var(--accent); }
  .slider-dots span:first-child { background: var(--white); }
  .hero-visual { position: absolute; left: 598px; top: 32px; width: 392px; height: 336px;
    background: linear-gradient(180deg, #66d12e 0%, #e6e8e9 55%, #d8c2b0 100%); border-radius: 3px; }
  .hero-shadow { position: absolute; left: 250px; top: 466px; width: 700px; height: 10px;
    background: radial-gradient(ellipse at top, rgba(0,0,0,0.45), rgba(0,0,0,0) 70%); }

  .plans-intro { position: absolute; left: 0; top: 508px; width: 1200px; text-align: center; font-family: "PT Sans", Arial, sans-serif; }
  .plans-intro h1 { font-weight: 400; font-size: 17px; letter-spacing: 0.2px; }
  .plans-intro p { margin-top: 25px; font-size: 18px; }

  .feature { position: absolute; top: 610px; width: 460px; height: 207px; background: var(--card-bg); }
  .feature-ssl { left: 123px; }
  .feature-uptime { left: 613px; }
  .feature h2 { position: absolute; left: 136px; top: 20px; font-family: "PT Sans", Arial, sans-serif; font-weight: 400; font-size: 18px; }
  .feature-icon { position: absolute; left: 15px; top: 51px; width: 102px; height: 103px; background: var(--white);
    display: flex; align-items: center; justify-content: center; }
  .feature p { position: absolute; left: 137px; top: 48px; width: 302px; font-size: 11.5px; line-height: 22px; text-align: justify; color: var(--ink); }
  .learn-more { position: absolute; right: 21px; top: 165px; width: 71px; height: 28px; border-radius: 3px; background: var(--accent);
    color: var(--ink); font-size: 12px; text-decoration: none; display: flex; align-items: center; justify-content: center; }

  .site-footer { position: absolute; left: 0; top: 855px; width: 1200px; height: 66px; background: var(--footer-bg); }
  .copyright { position: absolute; left: 123px; top: 25px; font-size: 12px; color: var(--footer-text); }
  .social-links { position: absolute; left: 872px; top: 16px; display: flex; gap: 10px; }
  .social-links a { width: 32px; height: 32px; border-radius: 50%; background: var(--social); display: block; }
</style>
</head>
<body>
  <header class="site-header">
    <div class="brand"><span class="brand-mark"></span>PINGO.QZ</div>
    <div class="contact-phone">
      <svg width="14" height="10" viewBox="0 0 14 10"><path d="M1 3 Q7 -1 13 3 L12 5 L9 4 L9 3 Q7 2 5 3 L5 4 L2 5 Z" fill="#888"/><rect x="3" y="5" width="8" height="4" rx="1" fill="#888"/></svg>
      020-55501234
    </div>
    <nav class="main-nav">
      <a href="#">How it Works</a>
      <a href="#">Support</a>
      <a href="#">Login</a>
    </nav>
  </header>

  <section class="hero">
    <ul class="hero-points">
      <li><svg class="tick" viewBox="0 0 13 13"><circle cx="6.5" cy="6.5" r="6.5" fill="#fff"/><path d="M3.5 6.8 L5.7 9 L9.7 4.6" stroke="#2e3a44" stroke-width="1.8" fill="none"/></svg>We make email easy</li>
      <li><svg class="tick" viewBox="0 0 13 13"><circle cx="6.5" cy="6.5" r="6.5" fill="#fff"/><path d="M3.5 6.8 L5.7 9 L9.7 4.6" stroke="#2e3a44" stroke-width="1.8" fill="none"/></svg>Give us five minutes and well get you email from your domain</li>
      <li><svg class="tick" viewBox="0 0 13 13"><circle cx="6.5" cy="6.5" r="6.5" fill="#fff"/><path d="M3.5 6.8 L5.7 9 L9.7 4.6" stroke="#2e3a44" stroke-width="1.8" fill="none"/></svg>Easily forward mail from your custom domain name wherever</li>
      <li><svg class="tick" viewBox="0 0 13 13"><circle cx="6.5" cy="6.5" r="6.5" fill="#fff"/><path d="M3.5 6.8 L5.7 9 L9.7 4.6" stroke="#2e3a44" stroke-width="1.8" fill="none"/></svg>You take the mail, we’ll keep the spam</li>
    </ul>
    <a class="cta cta-start" href="#">GET STARTED FREE</a>
    <a class="cta cta-plans" href="#">COMPARE PLANS</a>
    <div class="slider-dots"><span></span><span></span><span></span></div>
    <div class="hero-visual" role="img" aria-label="A finger opening a white envelope holding a green card with an at sign"></div>
  </section>
  <div class="hero-shadow"></div>

  <section class="plans-intro">
    <h1>PICK A PLAN AND GET STARTED IN ONE MINUTE</h1>
    <p>~ Lorem ipsum dolor sit amet, consectetuer adipiscing elitLorem ipsum dolor sit amet, consectetuer adipiscing elit ~</p>
  </section>

  <article class="feature feature-ssl">
    <h2>SECURE WITH SSL SUPPORT</h2>
    <div class="feature-icon">
      <svg width="62" height="72" viewBox="0 0 62 72"><path d="M14 32 V20 A17 17 0 0 1 48 20 V32" stroke="#000" stroke-width="8" fill="none"/><rect x="2" y="30" width="58" height="40" rx="3" fill="#000"/><circle cx="31" cy="48" r="6" fill="#fff"/></svg>
    </div>
    <p>Lorem ipsum dolor sit amet, adipiscing elit, sed diam non-ummy nibh euismod tincidunt ut laoreet dolore magna at vero eros aliquam erat volutpatLorem ipsum dolor sit amet, adipiscing elit, sed diam nonummy nibh euismod tincidunt ut laoreet dolore magna at vero eros</p>
    <a class="learn-more" href="#">Learn more</a>
  </article>

  <article class="feature feature-uptime">
    <h2>99.96% UPTIME GUARANTEED</h2>
    <div class="feature-icon">
      <svg width="76" height="76" viewBox="0 0 76 76">
        <g transform="translate(38 30)" fill="#000">
          <rect x="-5" y="-26" width="10" height="52" rx="1"/>
          <rect x="-5" y="-26" width="10" height="52" rx="1" transform="rotate(45)"/>
          <rect x="-5" y="-26" width="10" height="52" rx="1" transform="rotate(90)"/>
          <rect x="-5" y="-26" width="10" height="52" rx="1" transform="rotate(135)"/>
          <circle r="18"/>
          <circle r="7" fill="#fff"/>
        </g>
        <path d="M5 56 V72 H71 V56" stroke="#000" stroke-width="6" fill="none"/>
      </svg>
    </div>
    <p>Lorem ipsum dolor sit amet, adipiscing elit, sed diam non-ummy nibh euismod tincidunt ut laoreet dolore magna at vero eros aliquam erat volutpatLorem ipsum dolor sit amet, adipiscing elit, sed diam nonummy nibh euismod tincidunt ut laoreet dolore magna at vero eros</p>
    <a class="learn-more" href="#">Learn more</a>
  </article>

  <footer class="site-footer">
    <p class="copyright">© 2014. pingo.qz. All rights reserved.</p>
    <nav class="social-links" aria-label="Social networks">
      <a href="#" aria-label="Social network 1"></a>
      <a href="#" aria-label="Social network 2"></a>
      <a href="#" aria-label="Social network 3"></a>
      <a href="#" aria-label="Social network 4"></a>
      <a href="#" aria-label="Social network 5"></a>
    </nav>
  </footer>
</body>
</html>
```